Künstlerisches CD-Cover für Album
Zielgruppe
Ich bin ein Künstler im musikalischen Bereich. Meine Musikrichtung ist kombiniert aus den Bereichen des Rapps und dem Gesang. Mein Stil ist eher Gefühlvoll. Passend dazu suche ich ein echt künstleriches CD-Cover für mein Album >>> Spur im Nebel <<< .
Aufgabenstellung
Ich lege besonderen Wert auf echt kreative und künstlerische Fähigkeiten bei der Umsetzug des CD-Covers. Dieses Cover sollte ein echter Blickfang werden und zu meinem Album Namens >>>Spur im Nebel<<< passen.
Dabei ist folgendes Besonders zu Beachten:
(Albumtitel und mein Künstlername sollte auf die Frontansicht)
Spur im Nebel
Jonas Brehm
(Auf die Rückseite des Album-Covers sollten die Songtitel, Songlänge, Gesamtlänge sowie die weiteren Infos stehen)
1. Intro (Tobi) 1:06
2. Spur im Nebel 3:36
3. Traumfrau (feat. Sven) 3:52
4. Du bist weg 3:22
5. Denke positiv 3:09
6. Familie 2:44
7. Dir Mama 3:48
8. Letzte Sekunde 3:45
9. Liebe gesucht (feat. Sven) 3:15
10. Schöne Zeit 3:18
11. Ich bin da 3:21
12. Karma 2:47
13. Ich geh allein 3:13
14. Nicht gedacht 3:00
15. Sommer 2:51
16. Du bist frei 3:58
17. Schau nicht zurück 3:25
18. Spur im Nebel 3:36
58Min. 6Sek.
Texte & Songwriting by Jonas Brehm I Produziert im Nachtfalke Studio by Sven Ulrich Grabinski I Foto by Helmut K. Fotografie
(weitere Informationen)
>>> Das CD-Cover ist bestimmt für ein vierseitigen Druck und der CD (Voderseite, Rückseite, Innenseite Links, Innenseite Rechts und CD)
Das hochgeladene Fotomaterial sollte im Design mit eingebunden werden. Am besten wäre das Foto mit meiner Wenigkeit auf der Innenseite Links und das andere vorhandene Foto auf der CD selber zu intigrieren. Natürlich bin ich aber auch Offen für Alles und vertraue auf eure künstlerischen Fähigkeiten.
Viel Spaß :)

```html
<!DOCTYPE html>
<html lang="de">
<head>
<meta charset="utf-8">
<title>Spur im Nebel – Jonas Brehm</title>
<link rel="stylesheet" href="https://fonts.googleapis.com/css2?family=Allison&family=Fira+Sans+Condensed:wght@400&display=swap">
<style>
  :root {
    --black: #000000;
    --deep-red: #7a0a06;
    --red: #b3160d;
    --ember: #f08a12;
    --flame: #ffd24a;
    --blush: #f7d6cb;
    --ink: #ffffff;
    --silver: #c9c9c9;
    --hub: #8e8e8e;
  }
  * { margin: 0; padding: 0; box-sizing: border-box; }
  html, body { width: 1200px; height: 1199px; overflow: hidden; background: var(--black); }
  body { position: relative; font-family: "Fira Sans Condensed", "Arial Narrow", sans-serif; color: var(--ink); }

  .panel { position: absolute; overflow: hidden; }
  .back-cover { left: 0; top: 0; width: 600px; height: 600px; }
  .front-cover { left: 600px; top: 0; width: 600px; height: 600px; }
  .inner-left { left: 0; top: 600px; width: 600px; height: 599px; background: var(--black); }
  .inner-right { left: 600px; top: 600px; width: 600px; height: 599px; background: var(--black); }

  .fire-field { position: absolute; inset: 0; }
  .back-cover .fire-field {
    background:
      radial-gradient(circle at 92% 92%, var(--flame) 0, var(--ember) 8%, transparent 22%),
      radial-gradient(circle at 30% 3%, var(--flame) 0, var(--ember) 6%, transparent 18%),
      radial-gradient(ellipse at 12% 80%, #1a0000 0, transparent 25%),
      radial-gradient(ellipse at 55% 45%, var(--red) 0, var(--deep-red) 70%);
  }
  .front-cover .fire-field,
  .disc .fire-field {
    background: radial-gradient(ellipse at 65% 50%, rgba(180,20,10,.9) 0, var(--deep-red) 45%, #2a0000 85%);
  }
  .flame-heart {
    position: absolute;
    border-radius: 50% 50% 45% 45%;
    background: radial-gradient(ellipse at 50% 45%, transparent 42%, var(--ember) 50%, var(--flame) 56%, var(--ember) 62%, transparent 70%);
  }
  .front-cover .flame-heart { left: 150px; top: 90px; width: 400px; height: 440px; }

  .tracklist { position: absolute; left: 198px; top: 119px; width: 217px; list-style: none; font-size: 14.5px; line-height: 16.5px; letter-spacing: .3px; }
  .tracklist li { display: flex; justify-content: space-between; white-space: nowrap; }
  .credits { position: absolute; right: 185px; top: 470px; text-align: right; font-size: 12.5px; line-height: 14.5px; white-space: nowrap; }
  .credits p + p { margin-top: 4px; }

  .album-title { position: absolute; font-family: "Allison", cursive; color: var(--blush); font-weight: 400; font-size: 58px; line-height: 1; white-space: nowrap; }
  .artist-name { position: absolute; font-size: 13.5px; line-height: 1; color: var(--ink); white-space: nowrap; }
  .front-cover .album-title { left: 112px; top: 330px; }
  .front-cover .artist-name { left: 263px; top: 403px; }

  .artist-photo { position: absolute; left: 0; top: 0; width: 360px; height: 599px;
    background:
      linear-gradient(90deg, transparent 70%, var(--black) 100%),
      radial-gradient(ellipse at 40% 85%, #c0241a 0, transparent 18%),
      linear-gradient(180deg, #3b3a3c 0, #8d8c90 40%, #4f5b70 100%); }
  .inner-left .album-title { left: 345px; top: 86px; }
  .liner-notes { position: absolute; right: 61px; top: 182px; width: 190px; text-align: right; font-size: 12.5px; line-height: 14.1px; white-space: nowrap; }
  .liner-notes p + p { margin-top: 14px; }

  .disc { position: absolute; left: 33px; top: 26px; width: 524px; height: 524px; border-radius: 50%; overflow: hidden;
    border: 3px solid var(--silver); box-shadow: 0 0 0 1px #777; }
  .disc .flame-heart { left: 100px; top: 85px; width: 400px; height: 440px; }
  .disc-hub { position: absolute; left: 50%; top: 50%; width: 82px; height: 82px; margin: -41px 0 0 -41px; border-radius: 50%;
    background: radial-gradient(circle, var(--hub) 0 55%, #d9d9d9 62%, #9a9a9a 100%); }
  .disc .album-title { left: 64px; top: 312px; }
  .disc .artist-name { left: 212px; top: 383px; }
</style>
</head>
<body>

<section class="panel back-cover">
  <div class="fire-field" role="img" aria-label="Glühender roter Flammenhintergrund mit Funken"></div>
  <ol class="tracklist">
    <li><span>1. Intro (Tobi)</span><span>1:06</span></li>
    <li><span>2. Spur im Nebel</span><span>3:36</span></li>
    <li><span>3. Traumfrau (feat. Sven)</span><span>3:52</span></li>
    <li><span>4. Du bist weg</span><span>3:22</span></li>
    <li><span>5. Denke positiv</span><span>3:09</span></li>
    <li><span>6. Familie</span><span>2:44</span></li>
    <li><span>7. Dir Mama</span><span>3:48</span></li>
    <li><span>8. Letzte Sekunde</span><span>3:45</span></li>
    <li><span>9. Liebe gesucht (feat. Sven)</span><span>3:15</span></li>
    <li><span>10. Schöne Zeit</span><span>3:18</span></li>
    <li><span>11. Ich bin da</span><span>3:21</span></li>
    <li><span>12. Karma</span><span>2:47</span></li>
    <li><span>13. Ich geh allein</span><span>3:13</span></li>
    <li><span>14. Nicht gedacht</span><span>3:00</span></li>
    <li><span>15. Sommer</span><span>2:51</span></li>
    <li><span>16. Du bist frei</span><span>3:58</span></li>
    <li><span>17. Schau nicht zurück</span><span>3:25</span></li>
    <li><span>18. Spur im Nebel</span><span>3:36</span></li>
  </ol>
  <div class="credits">
    <p>Texte &amp; Songwriting by Jonas Brehm</p>
    <p>Produziert im Nachtfalke Studio<br>by Sven Ulrich Grabinski</p>
    <p>Foto by Helmut K. Fotografie</p>
  </div>
</section>

<section class="panel front-cover">
  <div class="fire-field" role="img" aria-label="Dunkelroter Flammenhintergrund"></div>
  <div class="flame-heart" role="img" aria-label="Herz aus lodernden Flammen mit Funken"></div>
  <h1 class="album-title">Spur im Nebel</h1>
  <p class="artist-name">Jonas Brehm</p>
</section>

<section class="panel inner-left">
  <div class="artist-photo" role="img" aria-label="Foto des Künstlers, hockend vor dunklem Fels, ein rotes Herz in den Händen"></div>
  <h2 class="album-title">Spur im Nebel</h2>
  <div class="liner-notes">
    <p>Lorem ipsum dolor sit amet,<br>consetetur sadipscing elitr, sed<br>diam nonumy eirmod tempor<br>invidunt ut labore et dolore<br>magna aliquyam erat, sed diam<br>voluptua. At vero eos et accusam<br>et justo duo dolores et ea rebum.</p>
    <p>Stet clita kasd gubergren,<br>no sea takimata sanctus est<br>Lorem ipsum dolor sit amet.<br>Lorem ipsum dolor sit amet,<br>ca rebum. Stet clita kasd<br>gubergren, no sea takimata<br>sanctus est Lorem ipsum<br>dolor sit amet.</p>
  </div>
</section>

<section class="panel inner-right">
  <div class="disc">
    <div class="fire-field" role="img" aria-label="Dunkelroter Flammenhintergrund"></div>
    <div class="flame-heart" role="img" aria-label="Herz aus lodernden Flammen mit Funken"></div>
    <p class="album-title">Spur im Nebel</p>
    <p class="artist-name">Jonas Brehm</p>
    <div class="disc-hub"></div>
  </div>
</section>

</body>
</html>
```